Laser Tattoo Removal Business Cards

We are looking for a professional business card design for a laser tattoo removal business. Ideally looking for a black business card design. The name of the business is Brightline Tattoo Removal. We place our cards at local tattoo shops so we ideally are looking for something trendy/edgy to draw both male and female clientele in.

Target Market(s)

Male/Female ages 18-60

Contact Information for Business Card

black background ideally.. hoping to stay within greys, whites and black

Font styles to use
Serif
Sans Serif

Colors
121212
a9a9a9
5c5c5c
f5f5f5
ffffff
7f7f7f
606060
848484
9d9d9d

Requirements
Must have
• Employee Info:
• Melissa Thornbury
• Chief Executive Offer
• m: 919.537.2846
• w: 919.362.4178
• f: 919.685.3907
• mthornbury@brightlinetattooremoval.example
• Address:
• 4615 Oakmere Pkwy, Suite 210
• Raleigh, NC 27654
• Website:
• www.brightlinetattooremoval.example
Nice to have
• Myabe business name on back or logo on back and employee info on the front

```html
<!DOCTYPE html>
<html lang="en">
<head>
<meta charset="utf-8">
<title>Brightline Tattoo Removal – Business Card</title>
<link rel="stylesheet" href="https://fonts.googleapis.com/css2?family=Lato:wght@400;700&family=Arimo:wght@400&display=swap">
<style>
  :root {
    --backdrop: #676767;
    --card: #121212;
    --ink: #ffffff;
    --ink-soft: #f5f5f5;
    --rule: #5c5c5c;
    --rule-light: #848484;
  }
  html, body {
    margin: 0;
    padding: 0;
    width: 1200px;
    height: 802px;
    overflow: hidden;
    background: var(--backdrop);
  }
  .canvas {
    position: relative;
    width: 1200px;
    height: 802px;
  }
  .card {
    position: absolute;
    top: 274px;
    width: 442px;
    height: 265px;
    background: var(--card);
    color: var(--ink);
    font-family: "Arimo", Arial, sans-serif;
  }
  .card--front { left: 136px; }
  .card--back { left: 624px; }

  .brand {
    position: absolute;
    text-align: center;
    font-family: "Lato", Arial, sans-serif;
    font-weight: 700;
    color: var(--ink-soft);
    line-height: 1;
  }
  .brand__mark {
    display: block;
    width: 10px;
    height: 10px;
    margin: 0 auto 10px;
    border-radius: 50%;
    background: var(--ink-soft);
  }
  .brand__name {
    display: block;
    font-size: 27px;
    letter-spacing: 2px;
  }
  .brand__line {
    display: block;
    margin-top: 10px;
    font-size: 10.5px;
    letter-spacing: 2.4px;
  }
  .card--front .brand { left: 14px; width: 200px; top: 95px; }
  .card--back .brand { left: 121px; width: 200px; top: 80px; }

  .divider {
    position: absolute;
    left: 222px;
    top: 60px;
    width: 1px;
    height: 140px;
    background: linear-gradient(to bottom, transparent, var(--rule) 20%, var(--rule) 80%, transparent);
  }

  .contact {
    position: absolute;
    left: 248px;
    top: 64px;
    font-size: 13px;
    line-height: 1.3;
  }
  .contact__name {
    margin: 0;
    font-family: "Lato", Arial, sans-serif;
    font-weight: 700;
    font-size: 16.5px;
    letter-spacing: 0.2px;
    line-height: 1.1;
  }
  .contact__title { margin: 0 0 10px; }
  .contact__phones { list-style: none; margin: 0 0 9px; padding: 0; }
  .contact__phones li { display: flex; align-items: center; height: 17px; }
  .contact__phones svg { width: 10px; height: 10px; margin-right: 6px; fill: var(--ink); }
  .contact__address { margin: 0; font-style: normal; }

  .back__rule {
    position: absolute;
    left: 117px;
    top: 184px;
    width: 206px;
    height: 1px;
    background: var(--rule);
  }
  .back__links {
    position: absolute;
    left: 0;
    top: 198px;
    width: 100%;
    text-align: center;
    font-size: 12.5px;
    line-height: 1.35;
    color: var(--ink-soft);
  }
  .back__links p { margin: 0; }
</style>
</head>
<body>
<div class="canvas">

  <section class="card card--front" aria-label="Business card front">
    <div class="brand">
      <span class="brand__mark"></span>
      <span class="brand__name">BRIGHTLINE</span>
      <span class="brand__line">TATTOO REMOVAL</span>
    </div>

    <div class="divider"></div>

    <div class="contact">
      <h1 class="contact__name">MELISSA THORNBURY</h1>
      <p class="contact__title">Chief Executive Officer</p>
      <ul class="contact__phones">
        <li>
          <svg viewBox="0 0 10 10" aria-label="Mobile"><path d="M2.5 0h5a1 1 0 0 1 1 1v8a1 1 0 0 1-1 1h-5a1 1 0 0 1-1-1V1a1 1 0 0 1 1-1zm.3 1.2v6.6h4.4V1.2z"/></svg>
          919.537.2846
        </li>
        <li>
          <svg viewBox="0 0 10 10" aria-label="Phone"><path d="M2 0.5l1.6 2.2-1 1.1c.6 1.3 1.5 2.2 2.7 2.8l1-1L8.6 7 7.5 9.4C4 9 1 6 .6 2.4z"/></svg>
          919.362.4178
        </li>
        <li>
          <svg viewBox="0 0 10 10" aria-label="Fax"><path d="M2.5 0h5v3h-5zM0.5 3.5h9v4h-2V6h-5v1.5h-2zM2.5 6.5h5V10h-5z"/></svg>
          919.685.3907
        </li>
      </ul>
      <address class="contact__address">4615 Oakmere Pkwy, Suite 210<br>Raleigh, NC 27654</address>
    </div>
  </section>

  <section class="card card--back" aria-label="Business card back">
    <div class="brand">
      <span class="brand__mark"></span>
      <span class="brand__name">BRIGHTLINE</span>
      <span class="brand__line">TATTOO REMOVAL</span>
    </div>
    <div class="back__rule"></div>
    <div class="back__links">
      <p>mthornbury@brightlinetattooremoval.example</p>
      <p>www.brightlinetattooremoval.example</p>
    </div>
  </section>

</div>
</body>
</html>
```